Brochure for a civil enineering company in A4 format

I need a brochure design for our company TIRO Engineering S.r.l.. We are an engineering consultant company. Our main clients are from the infrastructure industry (geotechnical and underground sectors mainly).
We are looking for a 2 pages (4 faces) fold out design with a glued pocket where we can put individual data sheets.
I need A4 format pages.

Target Market(s)

We are an engineering consultant company. Our main clients are from the infrastructure industry (geotechnical and underground sectors mainly).

Industry/Entity Type

Civil Engineer

Font styles to use
Sans Serif

Requirements
Must have
• Overall: 2 pages in A4 format
Essential style. Bright and modern appearance.
Glued pocket
Logo integrated in a picture on the pocket where I would like to insert a slogan (… tiro engineering … reliable solutions …)
Attached are selected images which the designer can use and edit at their own discretion.
Some advice in the following (anyway designers are free to provide their solutions):
Outer sheets:
Front page with name, logo. It could be nice to have the “m” of the logo integrated in a pictures, also a modified picture (I mean modify one of the attached pictures) so to create a general image and do not tie the cover to a specific job.
Back page: offices address and contact email address. Nice to have one space for a slogan.
Inner sheet: text that I upload in the file “inside-sheets”, possibly with pictures on each sheet. In the right faces insert the glued pocket. On this pages insert the section OUR EXPERIENCE ….with a space for a picture of our team.
Nice to have
• Clean and essential design.
Pictures choosing from the atteched ones. Pictures could be modified in a very light manner to make them a general idea of the work ( I mean geotechnical world) without to be immediately linked to a specific site.
Should not have
• excessive frills

```html
<!DOCTYPE html>
<html lang="en">
<head>
<meta charset="utf-8">
<title>TIRO Engineering – Fold-out Brochure</title>
<link href="https://fonts.googleapis.com/css2?family=Open+Sans:wght@400;600;700&display=swap" rel="stylesheet">
<style>
  :root{
    --stage:#2b2b2b;
    --paper:#ffffff;
    --ink:#1a1a1a;
    --band:#0b0b0b;
    --accent:#1a8bc2;
    --accent-edge:#cfe6f2;
    --muted:#555;
  }
  *{box-sizing:border-box;margin:0;padding:0}
  html,body{width:1200px;height:900px;overflow:hidden}
  body{background:var(--stage);font-family:"Open Sans",Arial,sans-serif;color:var(--ink);position:relative}
  .panel{position:absolute;top:111px;width:354px;height:501px;background:var(--paper);overflow:hidden}
  .panel--company{left:82px}
  .panel--contact{left:436px;background:linear-gradient(180deg,#fff 0%,#f1f1f1 45%,#e9e9e9 100%)}
  .panel--cover{left:790px;width:356px}

  .photo{position:absolute}
  .photo--bridge{left:0;top:0;width:354px;height:230px;
    background:linear-gradient(180deg,#b9d4ea 0%,#9fb7c4 18%,#6f7f5e 34%,#7c6a4f 52%,#b9a48a 72%,#f4f1ec 92%,#fff 100%)}
  .photo--site-faded{left:0;top:370px;width:354px;height:130px;
    background:linear-gradient(180deg,#fff 0%,#e8e8e8 40%,#cfcfcf 100%)}

  .pill{position:absolute;background:var(--accent);color:#fff;border-radius:14px;box-shadow:0 0 0 2px var(--accent-edge)}
  .pill--company{left:97px;top:242px;width:172px;height:26px;font-size:17px;line-height:26px;text-align:center;letter-spacing:.5px}
  .pill--company b{font-weight:700}
  .pill--contact{left:-14px;top:25px;width:190px;height:23px;padding-left:30px;font-size:17px;font-weight:700;line-height:23px;border-radius:0 12px 12px 0}

  .company-text{position:absolute;left:20px;width:318px;font-size:5.4px;line-height:7.2px;color:var(--muted)}
  .company-text--intro{top:283px}
  .company-cols{position:absolute;left:20px;top:316px;width:318px;display:flex;gap:10px}
  .company-cols p{flex:1;font-size:5.4px;line-height:7.2px;color:var(--muted)}
  .company-claim{position:absolute;left:20px;top:378px;width:318px;text-align:center;font-size:7.4px;line-height:9.6px;font-weight:600;color:#333}

  .web-band{position:absolute;left:0;bottom:0;width:100%;height:35px;background:var(--band);color:#fff;
    font-size:11px;letter-spacing:3px;text-align:center;line-height:35px}

  .office{position:absolute;top:60px}
  .office--left{left:43px}
  .office--right{left:207px;top:56px}
  .office h2{font-size:17px;font-weight:700;letter-spacing:.3px;margin-bottom:6px}
  .office p{font-size:12px;line-height:15px;color:#222}
  .office-divider{position:absolute;left:178px;top:62px;width:1px;height:62px;background:#bbb}
  .collage{position:absolute;left:0;top:0}

  .photo--landscape{left:0;top:45px;width:356px;height:385px;
    background:linear-gradient(180deg,#9ec3dd 0%,#8aa06a 16%,#7f8457 30%,#a4907a 48%,#c8b7a3 66%,#e9e3da 86%,#fff 100%)}
  .brand{position:absolute;left:46px;top:14px}
  .brand__name{font-size:50px;font-weight:700;line-height:52px;letter-spacing:1px;color:var(--ink)}
  .brand__line{font-size:6.5px;letter-spacing:1.6px;color:#222;margin-top:2px}
  .slogan{position:absolute;left:0;width:100%;text-align:center;color:#111}
  .slogan--name{top:392px;font-size:21px}
  .slogan--claim{top:418px;font-size:22px;letter-spacing:.5px}
</style>
</head>
<body>

<section class="panel panel--company">
  <div class="photo photo--bridge" role="img" aria-label="Photo of a viaduct under construction in a mountain valley"></div>
  <div class="pill pill--company">OUR <b>COMPANY</b></div>
  <p class="company-text company-text--intro">TIRO Engineering S.r.l. offre servizi di consulenza tecnica, contrattuale e strategica ai principali attori nei settori delle scienze geologiche, dell'ingegneria geotecnica e dell'ingegneria idraulica. Lavoriamo per mitigare il rischio e ridurre l'incertezza, con flessibilità nella ricerca della soluzione ottimale contribuendo ad aumentare la redditività del progetto.</p>
  <div class="company-cols">
    <p>TIRO Engineering S.r.l. è una società indipendente nata dall'unione di un gruppo di professionisti che hanno messo a fattor comune una lunga esperienza maturata nel settore delle grandi opere di ingegneria civile, come progettisti e consulenti.</p>
    <p>TIRO Engineering S.r.l. unisce l'esperienza dei fondatori all'entusiasmo di chi intraprende una nuova attività, con l'obiettivo principale di progettare infrastrutture sicure, sostenibili ed economiche per i clienti.</p>
  </div>
  <p class="company-claim">Each of our projects represents a long term commitment, we believe in providing safe, reliable, sustainable end innovative solutions. This is and will be our distinctive characteristic.</p>
  <div class="photo photo--site-faded" role="img" aria-label="Faded aerial photo of a construction site"></div>
  <div class="web-band">www.tiroengineering.org</div>
</section>

<section class="panel panel--contact">
  <div class="pill pill--contact">contact details</div>
  <div class="office office--left">
    <h2>LAGO TN</h2>
    <p>+39 02 555014400<br>20100 Milano &nbsp;- IT</p>
  </div>
  <div class="office-divider"></div>
  <div class="office office--right">
    <h2>VIA VERDI, 14</h2>
    <p>+39 02 555014400<br>Via S. MARCO, 9<br>32000 Lago TN - IT</p>
  </div>
  <svg class="collage" width="354" height="501" viewBox="0 0 354 501">
    <defs>
      <linearGradient id="g-city" x1="0" y1="0" x2="0" y2="1"><stop offset="0" stop-color="#a9c2d6"/><stop offset=".4" stop-color="#8b7a68"/><stop offset="1" stop-color="#cfc8bd"/></linearGradient>
      <linearGradient id="g-tunnel" x1="0" y1="0" x2="0" y2="1"><stop offset="0" stop-color="#6e7a4e"/><stop offset=".5" stop-color="#a08c6f"/><stop offset="1" stop-color="#8e8a82"/></linearGradient>
      <linearGradient id="g-crane" x1="0" y1="0" x2="1" y2="1"><stop offset="0" stop-color="#7d7468"/><stop offset=".5" stop-color="#a39585"/><stop offset="1" stop-color="#6d665e"/></linearGradient>
      <linearGradient id="g-hill" x1="0" y1="0" x2="0" y2="1"><stop offset="0" stop-color="#5f6e45"/><stop offset=".5" stop-color="#8f7f5f"/><stop offset="1" stop-color="#a9a091"/></linearGradient>
    </defs>
    <polygon points="0,290 150,310 205,345 125,495 0,480" fill="url(#g-city)" stroke="#fff" stroke-width="5" role="img" aria-label="Photo of an urban excavation beside buildings"/>
    <polygon points="0,189 190,133 212,284 0,319" fill="url(#g-tunnel)" stroke="#fff" stroke-width="5" role="img" aria-label="Photo of a tunnel portal and foundation works"/>
    <polygon points="160,300 250,178 354,262 354,372 282,400" fill="url(#g-crane)" stroke="#fff" stroke-width="5" role="img" aria-label="Aerial photo of a crane on a building site"/>
    <polygon points="104,410 346,340 354,490 124,501" fill="url(#g-hill)" stroke="#fff" stroke-width="5" role="img" aria-label="Photo of a tunnel entrance in green hills"/>
  </svg>
</section>

<section class="panel panel--cover">
  <div class="photo photo--landscape" role="img" aria-label="Photo of a hillside excavation site near the sea with orange safety fences"></div>
  <div class="brand">
    <div class="brand__name">tiro</div>
    <div class="brand__line">TIRO ENGINEERING , RELIABLE SOLUTIONS</div>
  </div>
  <p class="slogan slogan--name">tiro engineering</p>
  <p class="slogan slogan--claim">RELIABLE SOLUTIONS</p>
  <div class="web-band">www.tiroengineering.org</div>
</section>

</body>
</html>
```